Vantor Wear and Fuel is looking for a Clothing/Supplement Online Store Website!

Must be convenient, and user friendly, with vibrant colors that catch the eye!

Target Market(s)

Athletes, and Fashion Customers

Industry/Entity Type

Fitness

Coding

Coded - Design and coding required

Number of Pages Required

3 page

Font styles to use
Decorative

Colors

Designer to choose colors to be used in the design.

Requirements
Must have
• Somewhere to feature products, features to promote discounts and make announcements.
Nice to have
• My logos on each page

```html
<!DOCTYPE html>
<html lang="en">
<head>
<meta charset="utf-8">
<title>Vantor Wear and Fuel — Home</title>
<link href="https://fonts.googleapis.com/css2?family=Mulish:wght@400;600;700&display=swap" rel="stylesheet">
<style>
:root{
  --ink:#111;
  --text:#333;
  --muted:#8a8a8a;
  --topbar:#3b3b3b;
  --navbar:#e6e6e6;
  --black:#050505;
  --navy:#0f1b2e;
  --soft:#eeeeee;
  --card:#f4f4f4;
  --btn:#4a4a4a;
  --line:#d6d6d6;
  --white:#fff;
}
*{box-sizing:border-box;margin:0;padding:0}
html,body{width:1200px;height:4101px;overflow:hidden}
body{position:relative;font-family:"Mulish",sans-serif;color:var(--text);background:var(--white)}
.abs{position:absolute}
a{color:inherit;text-decoration:none}

/* top bar */
.topbar{left:0;top:0;width:1200px;height:40px;background:var(--topbar);color:#ddd;font-size:12px}
.topbar .left{left:100px;top:0;height:40px;display:flex;align-items:center;gap:22px}
.topbar .right{right:90px;top:0;height:40px;display:flex;align-items:center;gap:20px}

/* header */
.brand{font-weight:700;letter-spacing:2px;display:flex;align-items:center;gap:10px}
.brand .mark{width:14px;height:14px;background:currentColor}
.header-logo{left:89px;top:92px;font-size:40px;color:#222}
.search{left:360px;top:94px;width:485px;height:46px;border:1px solid #ccc;border-radius:23px;display:flex;align-items:center;font-size:12px;color:#999}
.search .q{flex:1;padding-left:28px}
.search .cat{width:160px;border-left:1px solid #ddd;height:100%;display:flex;align-items:center;padding-left:12px;font-size:14px}
.search .go{width:40px;height:40px;border-radius:50%;background:#555;margin-right:2px}
.cart{left:928px;top:94px;display:flex;align-items:center;gap:12px;font-size:14px;color:#222}
.cart .ic{width:46px;height:46px;border-radius:50%;background:#555}
.navbar{left:0;top:193px;width:1200px;height:44px;background:var(--navbar);display:flex;align-items:center;justify-content:center;gap:52px;font-size:17px;color:#555}

/* hero */
.hero{left:0;top:237px;width:1200px;height:630px}
.hero svg{position:absolute;left:0;top:0}
.hero-photo{left:660px;top:26px;width:500px;height:545px;background:radial-gradient(ellipse at 50% 45%,#8a6b58 0%,#4d3a30 35%,#141010 75%,transparent 100%)}
.hero-logo{left:89px;top:120px;font-size:56px;color:var(--white)}
.hero-copy{left:89px;top:200px;width:460px;font-size:22px;line-height:36px;color:var(--white)}
.btn-pill{left:89px;top:288px;width:204px;height:55px;border-radius:28px;background:#444;color:var(--white);font-size:17px;font-weight:700;display:flex;align-items:center;justify-content:center}
.dots{left:89px;top:372px;display:flex;gap:8px}
.dots span{width:13px;height:13px;border-radius:50%;background:var(--white)}
.dots span.on{background:transparent;border:2px solid #888}

/* features */
.feature{top:896px;width:249px;height:67px;border:1px solid #ccc;border-radius:34px;display:flex;align-items:center;gap:12px;padding-left:6px}
.feature .ic{width:55px;height:55px;border-radius:50%;background:#444}
.feature b{display:block;font-size:13px;font-weight:600;color:#222}
.feature small{font-size:12px;color:#999}

.section-title{left:0;width:1200px;text-align:center;font-size:36px;font-weight:600;color:#444}

/* product cards */
.product{width:250px;text-align:center}
.product .img{height:356px;background:var(--card);display:flex;align-items:center;justify-content:center}
.product .img div{width:200px;height:270px;border-radius:40px}
.tub{background:radial-gradient(ellipse at 50% 50%,#1a1a1a 0%,#2a2a2a 55%,var(--card) 72%)}
.hood-grey{background:radial-gradient(ellipse at 50% 50%,#cfcfcf 0%,#dcdcdc 55%,var(--card) 75%)}
.hood-black{background:radial-gradient(ellipse at 50% 50%,#151515 0%,#262626 55%,var(--card) 75%)}
.hood-blue{background:radial-gradient(ellipse at 50% 50%,#1e63d6 0%,#2f74e6 55%,var(--card) 75%)}
.product h3{font-size:20px;font-weight:400;color:#222;margin-top:14px}
.product p{font-size:15px;font-weight:700;color:#222;margin-top:4px}

/* promo bands */
.band-clothing{left:0;top:1580px;width:1200px;height:518px;background:linear-gradient(90deg,#0c1727,#14233a)}
.clothing-photo{left:620px;top:20px;width:480px;height:498px;background:radial-gradient(ellipse at 50% 55%,#2f5a8c 0%,#1d3659 40%,#122138 70%,transparent 100%)}
.band-title{font-size:46px;font-weight:600;color:var(--white)}
.band-rule{width:28px;height:3px;background:var(--white)}
.band-copy{font-size:18px;line-height:30px;color:var(--white);text-align:justify}
.btn-box{height:49px;background:var(--btn);color:var(--white);font-size:18px;display:flex;align-items:center;justify-content:center}
.arrivals{left:0;top:2098px;width:1200px;height:563px;background:var(--soft)}
.band-supp{left:0;top:2661px;width:1200px;height:517px;background:#0a0a0a}
.supp-photo{left:95px;top:10px;width:590px;height:507px;background:radial-gradient(ellipse at 45% 50%,#8c5e44 0%,#4a3a34 35%,#25272b 65%,#0a0a0a 100%)}

/* brands */
.brand-box{top:3298px;width:185px;height:109px;border:1px solid #ccc;display:flex;align-items:center;justify-content:center;font-size:22px;font-weight:700;color:#333}
.arrow{top:3340px;width:40px;height:24px}

/* footer */
.footer{left:0;top:3440px;width:1200px;height:661px}
.footer svg{position:absolute;left:0;top:0}
.pay{top:3648px;width:30px;height:17px;border-radius:2px}
.social{top:3642px;width:30px;height:30px;background:#555}
.footer-logo{left:0;width:1200px;top:3630px;justify-content:center;font-size:54px;color:var(--white)}
.contact-title{left:0;top:3725px;width:1200px;text-align:center;font-size:36px;color:var(--white)}
.col{top:3810px;width:355px;text-align:center;color:var(--white)}
.col .ic{width:22px;height:22px;margin:0 auto 20px}
.col h4{font-size:22px;font-weight:600;margin-bottom:14px}
.col p{font-size:13px;line-height:22px}
.divider{top:3808px;width:1px;height:134px;background:#555}
.bottom-rule{left:70px;top:4001px;width:1060px;height:1px;background:#444}
.bottom{top:4030px;font-size:13px;color:var(--white)}
.bottom-links{right:30px;display:flex;gap:28px}
</style>
</head>
<body>

<div class="abs topbar">
  <div class="abs left"><span>Store Location</span><span>Track Your Order</span><span>Login / Register</span></div>
  <div class="abs right"><span>Hotline: +1 555 014 2288</span><span>English ▾</span><span>USD ▾</span></div>
</div>

<div class="abs brand header-logo"><span class="mark"></span>VANTOR</div>
<div class="abs search"><span class="q">Search Product...</span><span class="cat">All Categories ▾</span><span class="go"></span></div>
<div class="abs cart"><span class="ic"></span><div>MY CART<br>0 item - <b>$0.00</b></div></div>
<nav class="abs navbar"><a>Protein</a><a>Performance</a><a>Weight Management</a><a>Vitamins &amp; Health</a><a>Clothing &amp; Accessories</a></nav>

<section class="abs hero">
  <svg width="1200" height="630" viewBox="0 0 1200 630">
    <path d="M0 500 L600 612 L1200 490 L1200 512 L600 630 L0 508 Z" fill="#6a6a6a"/>
    <path d="M0 0 H1200 V490 L600 612 L0 500 Z" fill="#050505"/>
  </svg>
  <div class="abs hero-photo" role="img" aria-label="Athlete in a grey zip hoodie showing his torso"></div>
  <div class="abs brand hero-logo"><span class="mark"></span>VANTOR</div>
  <p class="abs hero-copy">Sed ut perspiciatis unde omnis iste natus error sit voluptatem accusanti</p>
  <a class="abs btn-pill">GET STARTED ➜</a>
  <div class="abs dots"><span></span><span></span><span class="on"></span><span></span><span></span></div>
</section>

<div class="abs feature" style="left:76px"><span class="ic"></span><div><b>FREE SHIPPING</b><small>On Orders Over $49.00</small></div></div>
<div class="abs feature" style="left:344px"><span class="ic"></span><div><b>MONEY GUARANTEE</b><small>30 days back</small></div></div>
<div class="abs feature" style="left:610px"><span class="ic"></span><div><b>PAYMENT METHOD</b><small>Secure System</small></div></div>
<div class="abs feature" style="left:875px"><span class="ic"></span><div><b>ONLINE SUPPORT</b><small>24 hours a day</small></div></div>

<h2 class="abs section-title" style="top:1040px">FEATURE PRODUCTS</h2>
<div class="abs product" style="left:75px;top:1124px"><div class="img"><div class="hood-grey" role="img" aria-label="Grey hoodie"></div></div><h3>Grouped Product</h3><p>$ 106.59</p></div>
<div class="abs product" style="left:342px;top:1124px"><div class="img"><div class="tub" role="img" aria-label="Black supplement tub"></div></div><h3>Grouped Product</h3><p>$ 106.59</p></div>
<div class="abs product" style="left:608px;top:1124px"><div class="img"><div class="hood-black" role="img" aria-label="Black hoodie"></div></div><h3>Grouped Product</h3><p>$ 106.59</p></div>
<div class="abs product" style="left:875px;top:1124px"><div class="img"><div class="tub" role="img" aria-label="Black supplement tub"></div></div><h3>Grouped Product</h3><p>$ 106.59</p></div>

<section class="abs band-clothing">
  <div class="abs clothing-photo" role="img" aria-label="Athlete wearing a navy and white hoodie"></div>
  <h2 class="abs band-title" style="left:89px;top:110px">Clothing</h2>
  <div class="abs band-rule" style="left:89px;top:177px"></div>
  <p class="abs band-copy" style="left:89px;top:198px;width:346px">Lorem ipsum dolor sit amet, consecte adipiscing elit, sed do eiusmod tempor incididunt ut labore et dolore magna aliqua.</p>
  <a class="abs btn-box" style="left:89px;top:347px;width:176px">SHOP NOW</a>
</section>

<section class="abs arrivals"></section>
<h2 class="abs section-title" style="top:2132px">NEW ARRIVALS</h2>
<div class="abs product" style="left:75px;top:2203px"><div class="img"><div class="tub" role="img" aria-label="Black supplement tub"></div></div><h3>Grouped Product</h3><p>$ 106.59</p></div>
<div class="abs product" style="left:342px;top:2203px"><div class="img"><div class="hood-grey" role="img" aria-label="Grey pullover hoodie"></div></div><h3>Grouped Product</h3><p>$ 106.59</p></div>
<div class="abs product" style="left:608px;top:2203px"><div class="img"><div class="tub" role="img" aria-label="Black supplement tub"></div></div><h3>Grouped Product</h3><p>$ 106.59</p></div>
<div class="abs product" style="left:875px;top:2203px"><div class="img"><div class="hood-blue" role="img" aria-label="Blue pullover hoodie"></div></div><h3>Grouped Product</h3><p>$ 106.59</p></div>

<section class="abs band-supp">
  <div class="abs supp-photo" role="img" aria-label="Athlete with a towel holding an orange shaker bottle"></div>
  <h2 class="abs band-title" style="left:710px;top:124px;width:400px;text-align:center">Supplement</h2>
  <p class="abs band-copy" style="left:740px;top:210px;width:340px;text-align:center;line-height:35px">Lorem ipsum dolor sit amet, consectetur adipiscing elit, sed do labore et dolore magna aliqua.</p>
  <a class="abs btn-box" style="left:821px;top:334px;width:177px;height:46px">NEW ARRIVALS</a>
</section>

<h2 class="abs section-title" style="top:3222px">OUR BRAND</h2>
<svg class="abs arrow" style="left:37px" viewBox="0 0 40 24"><path d="M38 12H3M13 2L3 12l10 10" fill="none" stroke="#444" stroke-width="2.5"/></svg>
<div class="abs brand-box" style="left:105px;font-weight:400">Brimwell</div>
<div class="abs brand-box" style="left:306px">FORGELINE</div>
<div class="abs brand-box" style="left:508px">TALLPINE</div>
<div class="abs brand-box" style="left:708px;background:#f2f2f2">KESTRO</div>
<div class="abs brand-box" style="left:910px">Ovanta</div>
<svg class="abs arrow" style="left:1123px" viewBox="0 0 40 24"><path d="M2 12h35M27 2l10 10-10 10" fill="none" stroke="#444" stroke-width="2.5"/></svg>

<footer class="abs footer">
  <svg width="1200" height="661" viewBox="0 0 1200 661">
    <path d="M0 124 L600 14 L1200 124 V661 H0 Z" fill="#050505"/>
    <path d="M0 124 L600 0 L1200 124 L1200 130 L600 14 L0 132 Z" fill="#6a6a6a"/>
  </svg>
</footer>
<div class="abs pay" style="left:89px;background:#e9e9e9"></div>
<div class="abs pay" style="left:130px;background:#2a5fb0"></div>
<div class="abs pay" style="left:171px;background:#e9e9e9"></div>
<div class="abs pay" style="left:212px;background:#2a5fb0"></div>
<div class="abs brand footer-logo"><span class="mark"></span>VANTOR</div>
<div class="abs social" style="left:896px"></div>
<div class="abs social" style="left:940px"></div>
<div class="abs social" style="left:985px"></div>
<div class="abs social" style="left:1030px"></div>
<div class="abs social" style="left:1075px"></div>
<h2 class="abs contact-title">CONTACT INFORMATIONS</h2>

<div class="abs col" style="left:72px">
  <svg class="ic" viewBox="0 0 24 24"><path d="M6 2l4 4-2 3c1 3 4 6 7 7l3-2 4 4-3 4C10 22 2 14 2 5z" fill="#777"/></svg>
  <h4>CALL US</h4><p>(+555) 014 2288<br>(+555) 014 2288</p>
</div>
<div class="abs divider" style="left:412px"></div>
<div class="abs col" style="left:424px">
  <svg class="ic" viewBox="0 0 24 24"><path d="M12 3L2 12h3v9h5v-6h4v6h5v-9h3z" fill="#777"/></svg>
  <h4>FIND US</h4><p>No 18 Linden Row 402/7 Harbor City,<br>NY, United States</p>
</div>
<div class="abs divider" style="left:767px"></div>
<div class="abs col" style="left:780px">
  <svg class="ic" viewBox="0 0 24 24"><path d="M2 5h20v14H2z" fill="#777"/><path d="M2 5l10 8 10-8" fill="none" stroke="#050505" stroke-width="1.5"/></svg>
  <h4>EMAIL</h4><p>hello@vantorwear.com<br>care@vantorwear.com</p>
</div>

<div class="abs bottom-rule"></div>
<p class="abs bottom" style="left:89px">Vantor Wear and Fuel © 2019. All Rights Reserved.</p>
<div class="abs bottom bottom-links"><a>About</a><a>Legal infomation</a><a>Contact</a><a>Term of service</a><a>Privacy policy</a><a>C29</a></div>

</body>
</html>
```